I would like a single page website for Skyward Rentals Pacific. In the file list provided there is basic information to be included as well as our logo with colors, fonts and images to be included.
Site must be very simple and be able to be loaded onto smart phones etc very quickly.
Site needs to be very smart in appearance

Target Market(s)

All prospective drone customers from Police to Parties.

Industry/Entity Type

Hire

Requirements
Must have
• Must have variation of color schemes supplied
Nice to have
• Must be very eye catching without going over the top
Should not have
• Anything slow to load.

```html
<!DOCTYPE html>
<html lang="en">
<head>
<meta charset="utf-8">
<title>Skyward Rentals Pacific</title>
<link href="https://fonts.googleapis.com/css2?family=Titillium+Web:wght@600;700&family=Open+Sans:wght@400;600;700&display=swap" rel="stylesheet">
<style>
:root{
  --green:#5ea320;
  --green-dark:#4e8c18;
  --ink:#2b2b2b;
  --text:#555;
  --nav:#1c1c1c;
  --footer:#1e1e1e;
  --pale:#f2f2f2;
  --white:#fff;
}
*{margin:0;padding:0;box-sizing:border-box}
html,body{width:804px;height:1200px;overflow:hidden;background:var(--white)}
body{position:relative;font-family:"Open Sans",sans-serif;color:var(--text)}
.abs{position:absolute}
.head-font{font-family:"Titillium Web",sans-serif;font-weight:700}

/* header */
.site-header{position:absolute;left:0;top:0;width:804px;height:79px;background:var(--white)}
.brand{left:66px;top:18px;display:flex;align-items:center;gap:8px}
.brand-dot{width:14px;height:14px;border-radius:50%;background:var(--green)}
.brand-name{font-family:"Titillium Web",sans-serif;font-weight:700;font-size:19px;color:var(--green);line-height:1.1;width:150px}
.contact{left:388px;top:29px;display:flex;gap:8px;align-items:flex-start}
.contact .phone{font-family:"Titillium Web",sans-serif;font-weight:700;font-size:15px;color:var(--green);line-height:16px}
.contact .mail{font-size:7.5px;color:var(--ink);margin-top:2px}
.search{left:543px;top:32px;width:193px;height:27px;border:1px solid #d4d4d4;border-radius:2px;background:var(--white)}
.search span{position:absolute;left:9px;top:8px;font-size:7.5px;color:#888}
.search-btn{position:absolute;right:-1px;top:-1px;width:27px;height:27px;background:var(--green);border-radius:0 2px 2px 0}

/* nav */
.main-nav{position:absolute;left:0;top:79px;width:804px;height:35px;background:var(--nav)}
.main-nav a{position:absolute;top:0;height:35px;display:flex;align-items:center;justify-content:center;gap:7px;color:var(--white);text-decoration:none;font-size:8px;font-weight:700;letter-spacing:.2px;border-right:1px solid #2c2c2c}
.main-nav a.active{background:var(--green)}

/* hero */
.hero{position:absolute;left:0;top:114px;width:804px;height:341px}
.hero-bg{position:absolute;inset:0;background:linear-gradient(120deg,#2f3c4b 0%,#4c6078 40%,#6a7e96 65%,#3d4a58 100%)}
.hero-drone{position:absolute;left:430px;top:26px;width:220px;height:140px;border-radius:40%;background:radial-gradient(ellipse at center,rgba(240,242,245,.85),rgba(200,208,218,.35) 60%,rgba(200,208,218,0) 75%)}
.hero h1{position:absolute;left:65px;top:96px;width:380px;font-family:"Titillium Web",sans-serif;font-weight:700;font-size:21px;line-height:32px;color:var(--white);letter-spacing:.4px}
.hero p{position:absolute;left:67px;top:160px;width:340px;font-size:9.5px;line-height:20px;color:#eef1f4}
.btn{position:absolute;background:var(--green);color:var(--white);font-size:7px;font-weight:700;display:flex;align-items:center;justify-content:center;letter-spacing:.2px}
.hero-arrow{position:absolute;top:150px}

/* welcome */
.welcome-photo{left:67px;top:476px;width:245px;height:165px;background:linear-gradient(180deg,#7fa6dc 0%,#9cbde6 55%,#8fb27a 100%);box-shadow:0 14px 18px -12px rgba(0,0,0,.35)}
.welcome h2{position:absolute;left:330px;top:474px;font-size:14px;color:var(--ink)}
.green{color:var(--green)}
.rule{position:absolute;height:1px;background:#bbb}
.rule-accent{position:absolute;height:2px;background:var(--green)}
.welcome p{position:absolute;left:332px;width:365px;font-size:7.3px;line-height:13.7px;color:var(--text)}

/* services */
.services{position:absolute;left:0;top:664px;width:804px;height:246px;background:var(--pale)}
.section-title{position:absolute;font-family:"Titillium Web",sans-serif;font-weight:700;font-size:14.5px;color:var(--ink)}
.service{position:absolute;top:68px;width:200px;text-align:center}
.service .ring{margin:0 auto;width:64px;height:64px;border-radius:50%;border:1.5px solid #333;display:flex;align-items:center;justify-content:center}
.service.on .ring{border-color:var(--green)}
.service h3{font-family:"Titillium Web",sans-serif;font-weight:700;font-size:11px;color:var(--ink);margin-top:10px;letter-spacing:.2px}
.service p{font-size:7.3px;line-height:14.5px;color:var(--text);margin-top:3px}
.service .more{display:inline-block;margin-top:8px;width:66px;height:21px;border:1.5px solid #333;font-size:7.5px;line-height:18px;color:var(--ink)}
.service.on .more{border-color:var(--green);color:var(--green)}

/* works */
.works-list{position:absolute;list-style:none;font-size:7.3px;line-height:13.5px;color:var(--text)}
.works-list li{position:absolute;padding-left:14px;width:190px}
.works-list li svg{position:absolute;left:0;top:3px}
.works-video{left:457px;top:938px;width:240px;height:175px;background:linear-gradient(180deg,#a9b3bd 0%,#8d98a3 55%,#5f7a45 80%,#4a6634 100%);box-shadow:0 14px 18px -12px rgba(0,0,0,.35)}
.play{position:absolute;left:104px;top:71px;width:32px;height:32px;border-radius:50%;background:var(--white);display:flex;align-items:center;justify-content:center}

/* footer */
.site-footer{position:absolute;left:0;top:1132px;width:804px;height:68px;background:var(--footer);color:#e6e6e6}
.footer-links{position:absolute;left:66px;top:17px;font-size:7.5px}
.social{position:absolute;left:66px;top:36px;display:flex;gap:2px}
.social span{width:16px;height:16px;border-radius:50%;border:1px solid #bbb}
.copyright{position:absolute;left:549px;top:27px;font-size:7px;color:#cfcfcf}
</style>
</head>
<body>

<header class="site-header">
  <div class="abs brand"><span class="brand-dot"></span><span class="brand-name">Skyward Rentals Pacific</span></div>
  <div class="abs contact">
    <svg width="16" height="24" viewBox="0 0 16 24"><path d="M4 1 L8 4 L6 8 C5 11 6 15 9 18 L12 16 L15 20 L12 23 C6 22 1 14 2 4 Z" fill="#5ea320"/></svg>
    <div><div class="phone">0400 555 210</div><div class="mail">hello@skywardrentals.example</div></div>
  </div>
  <div class="abs search"><span>Enter your keyword...</span>
    <div class="search-btn"><svg width="27" height="27" viewBox="0 0 27 27"><circle cx="12.5" cy="12.5" r="3.5" fill="none" stroke="#fff" stroke-width="1.6"/><path d="M15 15 L18 18" stroke="#fff" stroke-width="1.8"/></svg></div>
  </div>
</header>

<nav class="main-nav">
  <a class="active" href="#" style="left:67px;width:95px"><svg width="10" height="9" viewBox="0 0 10 9"><path d="M5 0 L10 4.5 H8.5 V9 H6 V6 H4 V9 H1.5 V4.5 H0 Z" fill="#fff"/></svg>HOME</a>
  <a href="#" style="left:162px;width:108px"><svg width="9" height="9" viewBox="0 0 9 9"><circle cx="4.5" cy="2.5" r="2.3" fill="#fff"/><path d="M0 9 C0 5 9 5 9 9 Z" fill="#fff"/></svg>ABOUT US</a>
  <a href="#" style="left:270px;width:117px"><svg width="8" height="10" viewBox="0 0 8 10"><path d="M6 0 L1 6 H4 L2 10 L7 4 H4 Z" fill="#fff"/></svg>SERVICES</a>
  <a href="#" style="left:387px;width:109px">FEATURES<svg width="14" height="6" viewBox="0 0 14 6"><path d="M8 1 L10.5 3.5 L13 1" fill="none" stroke="#fff" stroke-width="1"/></svg></a>
  <a href="#" style="left:496px;width:125px"><svg width="9" height="9" viewBox="0 0 9 9"><path d="M7 0 L9 2 L3 8 L0 9 L1 6 Z" fill="#fff"/></svg>CAREERS</a>
  <a href="#" style="left:621px;width:117px"><svg width="10" height="7" viewBox="0 0 10 7"><rect width="10" height="7" fill="#fff"/><path d="M0 0 L5 4 L10 0" fill="none" stroke="#1c1c1c" stroke-width="1"/></svg>CONTACT US</a>
</nav>

<section class="hero">
  <div class="hero-bg" role="img" aria-label="Construction cranes and a glass tower under a blue sky with a white camera drone hovering"></div>
  <div class="hero-drone"></div>
  <h1>SPECIAL OCCASIONS, CHILDREN’S BIRTHDAY PARTIES</h1>
  <p>AVSA certified company and AVSA endorsed pilot, with Full Public Liability Insurance. All operating licences are in place and are carried on the operator</p>
  <div class="btn" style="left:66px;top:212px;width:79px;height:23px">VIEW MORE</div>
  <svg class="hero-arrow" style="left:30px" width="14" height="38" viewBox="0 0 14 38"><path d="M12 1 L2 19 L12 37" fill="none" stroke="#fff" stroke-width="1"/></svg>
  <svg class="hero-arrow" style="left:762px" width="14" height="38" viewBox="0 0 14 38"><path d="M2 1 L12 19 L2 37" fill="none" stroke="#fff" stroke-width="1"/></svg>
</section>

<section class="welcome">
  <div class="abs welcome-photo" role="img" aria-label="White quadcopter drone flying against a blue sky with green leaves"></div>
  <h2 class="head-font">WELCOME TO <span class="green">SKYWARD RENTALS</span> PACIFIC</h2>
  <div class="rule" style="left:330px;top:498px;width:263px"></div>
  <div class="rule-accent" style="left:330px;top:497px;width:16px"></div>
  <p style="top:509px">AVSA certified company and AVSA endorsed pilot, with Full Public Liability Insurance. All operating licences are in place and are carried on the operator. All drones are maintained to full AVSA compliance standards.Nemo enim ipsam voluptatem quia voluptas sit aspernatur aut odit aut fugit, sed quia consequuntur magni dolores eos qui ratione voluptatem sequi nesciunt.</p>
  <p style="top:575px">Nemo enim ipsam voluptatem quia voluptas sit aspernatur aut odit aut fugit, sed quia consequuntur magni dolores eos qui ratione voluptatem sequi nesciunt.</p>
  <div class="btn" style="left:332px;top:617px;width:81px;height:24px">MORE DETAILS</div>
</section>

<section class="services">
  <div class="section-title" style="left:353px;top:22px">OUR <span class="green">SERVICES</span></div>
  <div class="rule" style="left:342px;top:45px;width:110px"></div>
  <div class="rule-accent" style="left:392px;top:44px;width:18px"></div>

  <div class="service" style="left:86px">
    <div class="ring"><svg width="30" height="30" viewBox="0 0 30 30"><path d="M15 2 L18.5 11 L28 11 L20.5 17 L23.5 27 L15 21 L6.5 27 L9.5 17 L2 11 L11.5 11 Z" fill="#2b2b2b"/></svg></div>
    <h3>PARTIES</h3>
    <p>Lorem Ipsum is simply dummy text<br>of the printing and typesetting</p>
    <span class="more">More info</span>
  </div>
  <div class="service" style="left:298px">
    <div class="ring"><svg width="30" height="30" viewBox="0 0 30 30"><rect x="8" y="5" width="18" height="10" rx="2" transform="rotate(18 17 10)" fill="#2b2b2b"/><rect x="9" y="16" width="3" height="8" fill="#2b2b2b"/><rect x="4" y="22" width="8" height="3" fill="#2b2b2b"/></svg></div>
    <h3>SURVEILLANCE</h3>
    <p>Lorem Ipsum is simply dummy text<br>of the printing and typesetting</p>
    <span class="more">More info</span>
  </div>
  <div class="service on" style="left:521px">
    <div class="ring"><svg width="30" height="30" viewBox="0 0 30 30"><path d="M10 14 V10 A5 5 0 0 1 20 10 V14" fill="none" stroke="#5ea320" stroke-width="3"/><rect x="7" y="13" width="16" height="14" rx="1.5" fill="#5ea320"/><rect x="14" y="18" width="2" height="5" fill="#fff"/></svg></div>
    <h3>HIGHLY RELIABLE &amp; SECURITY</h3>
    <p>Lorem Ipsum is simply dummy text<br>of the printing and typesetting</p>
    <span class="more">More info</span>
  </div>
</section>

<section class="works">
  <div class="section-title" style="left:66px;top:934px">OUR <span class="green">WORKS</span></div>
  <div class="rule" style="left:66px;top:958px;width:79px"></div>
  <div class="rule-accent" style="left:66px;top:957px;width:16px"></div>
  <ul class="works-list">
    <li style="left:66px;top:972px"><svg width="9" height="8" viewBox="0 0 9 8"><path d="M1 4 L3.5 6.5 L8 1" fill="none" stroke="#5ea320" stroke-width="2"/></svg>Special Occasions, Children’s Birthday Parties, Weddings</li>
    <li style="left:66px;top:1006px"><svg width="9" height="8" viewBox="0 0 9 8"><path d="M1 4 L3.5 6.5 L8 1" fill="none" stroke="#5ea320" stroke-width="2"/></svg>Sporting events –4K Video of yourself participating in marathons etc</li>
    <li style="left:66px;top:1040px"><svg width="9" height="8" viewBox="0 0 9 8"><path d="M1 4 L3.5 6.5 L8 1" fill="none" stroke="#5ea320" stroke-width="2"/></svg>Real Estate Brochures</li>
    <li style="left:66px;top:1064px"><svg width="9" height="8" viewBox="0 0 9 8"><path d="M1 4 L3.5 6.5 L8 1" fill="none" stroke="#5ea320" stroke-width="2"/></svg>Surveillance – Police, Local councilsworksafeetc</li>
    <li style="left:271px;top:971px"><svg width="9" height="8" viewBox="0 0 9 8"><path d="M1 4 L3.5 6.5 L8 1" fill="none" stroke="#5ea320" stroke-width="2"/></svg>Building/Roof Condition Inspections</li>
    <li style="left:271px;top:1004px"><svg width="9" height="8" viewBox="0 0 9 8"><path d="M1 4 L3.5 6.5 L8 1" fill="none" stroke="#5ea320" stroke-width="2"/></svg>Lost pets</li>
    <li style="left:271px;top:1038px"><svg width="9" height="8" viewBox="0 0 9 8"><path d="M1 4 L3.5 6.5 L8 1" fill="none" stroke="#5ea320" stroke-width="2"/></svg>Accident reconstructions</li>
    <li style="left:271px;top:1066px"><svg width="9" height="8" viewBox="0 0 9 8"><path d="M1 4 L3.5 6.5 L8 1" fill="none" stroke="#5ea320" stroke-width="2"/></svg>Insurance assessing</li>
  </ul>
  <div class="btn" style="left:67px;top:1090px;width:81px;height:24px">MORE DETAILS</div>
  <div class="abs works-video" role="img" aria-label="Video still of two operators flying a large octocopter over a grassy field">
    <div class="play"><svg width="14" height="14" viewBox="0 0 14 14"><path d="M3 1 L13 7 L3 13 Z" fill="#333"/></svg></div>
  </div>
</section>

<footer class="site-footer">
  <div class="footer-links">Home |About us | Services | Features | Careers | Contact us</div>
  <div class="social"><span></span><span></span><span></span><span></span><span></span></div>
  <div class="copyright">Copyright © skywardrentalspacific. 2015 - All rights reserved</div>
</footer>

</body>
</html>
```